Torvane Halbridge

Looking for modern business cards.
Clean contemporary design.
Similar to this.
https://www.plumvexa-search.example/imgres?imgurl=https%3A%2F%2Fimg.quorlint-cdn.example%2Fsleek_dark_metal_card_design_540.jpg&imgrefurl=https%3A%2F%2Fwww.quorlint-prints.example%2Fsleek_dark_metal_card_design-918273645501928374&q=modern%20business%20cards

But I'd like the blue to look metallic.

Business

```html
<!DOCTYPE html>
<html lang="en">
<head>
<meta charset="utf-8">
<title>Torvane Halbridge – Business Card</title>
<link href="https://fonts.googleapis.com/css2?family=Roboto:wght@400;500&family=Roboto+Condensed:wght@400;500&display=swap" rel="stylesheet">
<style>
  :root {
    --backdrop: #6f4a30;
    --card-white: #f4f4f4;
    --navy-teal: #1f5068;
    --blue: #249cba;
    --blue-light: #5fc3dc;
    --blue-deep: #17708a;
    --text-grey: #555555;
    --white: #ffffff;
  }
  * { margin: 0; padding: 0; box-sizing: border-box; }
  html, body { width: 1200px; height: 960px; overflow: hidden; }
  body {
    position: relative;
    background: var(--backdrop);
    font-family: "Roboto", Arial, sans-serif;
  }
  .card {
    position: absolute;
    width: 600px;
    height: 343px;
    overflow: hidden;
    box-shadow: 0 3px 6px rgba(0,0,0,0.35);
  }
  .card-front { left: 314px; top: 113px; background: var(--card-white); }
  .card-back {
    left: 311px; top: 472px;
    background: linear-gradient(135deg, var(--blue-deep) 0%, var(--blue) 30%, var(--blue-light) 50%, var(--blue) 70%, var(--blue-deep) 100%);
  }
  .corner-art { position: absolute; inset: 0; }
  .brand {
    position: absolute;
    right: 60px; top: 58px;
    display: flex; align-items: center; gap: 8px;
  }
  .brand-name {
    font-family: "Roboto", Arial, sans-serif;
    font-weight: 400;
    font-size: 25px;
    color: var(--navy-teal);
    letter-spacing: -0.3px;
  }
  .brand-dot {
    width: 12px; height: 12px; border-radius: 50%;
    background: var(--blue);
  }
  .person {
    position: absolute;
    right: 72px; top: 115px;
    text-align: right;
    font-family: "Roboto Condensed", Arial, sans-serif;
  }
  .person-name { font-weight: 500; font-size: 20px; color: var(--navy-teal); line-height: 24px; }
  .person-role { font-weight: 400; font-size: 15px; color: var(--blue); line-height: 22px; }
  .address {
    position: absolute; left: 39px; top: 174px;
    font-size: 14px; line-height: 18px; color: var(--text-grey);
  }
  .contact-list {
    position: absolute; left: 39px; top: 221px;
    list-style: none;
    font-size: 14px; color: var(--text-grey);
  }
  .contact-list li { display: flex; align-items: center; height: 19.5px; }
  .contact-list svg { width: 13px; height: 13px; margin-right: 10px; fill: var(--navy-teal); }
  .back-brand {
    position: absolute; left: 0; right: 0; top: 138px;
    display: flex; justify-content: center; align-items: center; gap: 12px;
  }
  .back-brand .brand-name { color: var(--white); font-size: 40px; }
  .back-brand .brand-dot { width: 18px; height: 18px; background: var(--white); }
  .back-url {
    position: absolute; left: 0; right: 0; top: 299px;
    text-align: center;
    font-size: 14px; letter-spacing: 3px; color: var(--white);
  }
</style>
</head>
<body>
  <section class="card card-front">
    <svg class="corner-art" viewBox="0 0 600 343" aria-hidden="true">
      <defs>
        <linearGradient id="metal-blue" x1="0" y1="0" x2="1" y2="1">
          <stop offset="0" stop-color="#17708a"/>
          <stop offset="0.5" stop-color="#6cc8e0"/>
          <stop offset="1" stop-color="#1d8eab"/>
        </linearGradient>
      </defs>
      <path d="M0 0 H130 C62 22 16 70 0 128 Z" fill="var(--navy-teal)"/>
      <path d="M140 0 C70 22 18 72 3 138 C26 75 72 28 140 0 Z" fill="url(#metal-blue)" stroke="url(#metal-blue)" stroke-width="3"/>
      <path d="M600 343 H470 C540 320 586 274 600 212 Z" fill="var(--navy-teal)"/>
      <path d="M462 343 C532 320 584 272 598 205 C592 282 540 326 462 343 Z" fill="url(#metal-blue)"/>
    </svg>

    <div class="brand">
      <span class="brand-name">Torvane Halbridge</span>
      <span class="brand-dot"></span>
    </div>

    <div class="person">
      <p class="person-name">MAREN OSTROWE</p>
      <p class="person-role">CEO/FOUNDER</p>
    </div>

    <address class="address" style="font-style:normal">
      4120 Kestrel Row<br>
      Dunmere, Ohio 40918
    </address>

    <ul class="contact-list">
      <li><svg viewBox="0 0 16 16"><path d="M3.5 1 L6 1 L7 5 L5.2 6.4 C6 8.2 7.8 10 9.6 10.8 L11 9 L15 10 L15 12.5 C15 13.8 14 15 12.5 15 C6.5 14.5 1.5 9.5 1 3.5 C1 2 2.2 1 3.5 1 Z"/></svg>555 014 2290</li>
      <li><svg viewBox="0 0 16 16"><path d="M4 0 H12 A1 1 0 0 1 13 1 V15 A1 1 0 0 1 12 16 H4 A1 1 0 0 1 3 15 V1 A1 1 0 0 1 4 0 Z M4.5 2 V12.5 H11.5 V2 Z M8 13.3 A0.9 0.9 0 1 0 8 15.1 A0.9 0.9 0 1 0 8 13.3 Z"/></svg>555 016 7731</li>
      <li><svg viewBox="0 0 16 16"><path d="M4 1 H12 V5 H4 Z M1 6 H15 V13 H12 V11 H4 V13 H1 Z M5 12 H11 V15 H5 Z"/></svg>555 019 4086</li>
      <li><svg viewBox="0 0 16 16"><path d="M1 3 H15 V13 H1 Z M2.2 4.2 L8 8.6 L13.8 4.2 Z" fill-rule="evenodd"/></svg>maren@halbridge.example</li>
      <li><svg viewBox="0 0 16 16"><path d="M8 1 A7 7 0 1 0 8 15 A7 7 0 1 0 8 1 Z M5 4 C6.5 4.5 7 5.5 6 6.5 C5 7.5 6.5 8.5 7.5 9 C8 10.5 7 12 6.5 13 C3.5 12 2 9.5 2.5 6.5 C3 5 4 4 5 4 Z M10 3 C12 4 13.5 6 13 9 C12 9.5 11 9 10.5 8 C10 6.5 9 5.5 10 3 Z"/></svg>www.halbridge.example</li>
    </ul>
  </section>

  <section class="card card-back">
    <div class="back-brand">
      <span class="brand-name">Torvane Halbridge</span>
      <span class="brand-dot"></span>
    </div>
    <p class="back-url">www.torvanehalbridge.example</p>
  </section>
</body>
</html>
```